I need a business card for my original fine art pieces

I would like a business card design including a logo design for a new business in the art world. I am based in the Hunter Valley NSW Australia. I am a contemporary figurative, encaustic and wildlife artist. I would like to be able to upload my email and mobile number to this as well. This design should be one that I can incorporate into banners and flyers etc. Id like to incorporate one of my own images or partial image into the background or somewhere below. My initials are RJ and I would like these used as a logo type. I would like the use of some colour and it to be bright and catchy. The final design should communicate artwork custom made and commissions available.

Overview: Original Fine Artworks for sale, online, art galleries etc, Custom made to order and by commission.

Target market is world wide audience and corporate world

My figurative work is painted using acrylics in a lot of natural ochre colours that reflect the Australian Outback, on canvas, linen, paper or board: My encaustic work is created in a contemporary abstract style using a blow torch and a made with a medium of 100% pure bees wax, Damar resin, mixed media and coloured pigments, applied to Birch board. My wildlife are created using coloured pencil and mixed media on a variety of paper types or board.

```html
<!DOCTYPE html>
<html lang="en">
<head>
<meta charset="utf-8">
<title>Rita Jameson – Business Card</title>
<link rel="stylesheet" href="https://fonts.googleapis.com/css2?family=Open+Sans:wght@400;600&family=Montserrat:wght@500&display=swap">
<style>
  :root {
    --bg: #e9e6e3;
    --orange: #ff4500;
    --charcoal: #262626;
    --white: #ffffff;
    --ink: #1a1a1a;
  }
  * { margin: 0; padding: 0; box-sizing: border-box; }
  html, body { width: 1200px; height: 900px; overflow: hidden; }
  body { background: var(--bg); position: relative; font-family: "Open Sans", Arial, sans-serif; }

  .card { position: absolute; box-shadow: 0 8px 24px rgba(0,0,0,.18); }

  /* Front card */
  .card-front { left: 238px; top: 60px; width: 555px; height: 345px; background: var(--white); }
  .front-panel { position: absolute; left: 0; top: 0; width: 417px; height: 100%; background: var(--orange); }
  .front-band { position: absolute; left: 425px; top: 0; width: 130px; height: 100%; background: var(--charcoal); }
  .front-mark {
    position: absolute; left: 326px; top: 85px; width: 176px; height: 176px;
    border-radius: 50%; background: var(--white);
    display: flex; align-items: center; justify-content: center;
  }
  .mark-name {
    font-family: "Open Sans", Arial, sans-serif; font-weight: 600; font-size: 17px;
    letter-spacing: 1px; text-transform: uppercase; color: var(--orange); white-space: nowrap;
  }
  .holder { position: absolute; left: 37px; top: 50px; color: var(--white); }
  .holder-name { font-weight: 600; font-size: 18px; line-height: 22px; }
  .holder-title { font-size: 14.5px; line-height: 18px; }
  .address { position: absolute; left: 37px; top: 182px; color: var(--white); font-size: 14.5px; line-height: 20px; }
  .contacts { position: absolute; left: 37px; top: 236px; list-style: none; color: var(--white); font-size: 14.5px; }
  .contacts li { display: flex; align-items: center; height: 20px; }
  .contacts svg { width: 11px; height: 11px; margin-right: 9px; fill: var(--white); }

  /* Back card */
  .card-back { left: 457px; top: 518px; width: 560px; height: 344px; background: var(--white); }
  .back-circle {
    position: absolute; left: 223px; top: 88px; width: 114px; height: 114px;
    border: 3px solid var(--orange); border-radius: 50%;
  }
  .brand-name {
    position: absolute; left: 0; right: 0; top: 202px; text-align: center;
    font-family: "Open Sans", Arial, sans-serif; font-weight: 600; font-size: 29px;
    letter-spacing: 2px; text-transform: uppercase; color: var(--orange); line-height: 38px;
  }
  .brand-tagline {
    position: absolute; left: 0; right: 0; top: 241px; text-align: center;
    font-family: "Montserrat", Arial, sans-serif; font-weight: 500; font-size: 15px;
    letter-spacing: 3.3px; color: var(--ink);
  }
</style>
</head>
<body>

<section class="card card-front">
  <div class="front-panel"></div>
  <div class="front-band"></div>

  <div class="front-mark"><span class="mark-name">Rita Jameson</span></div>

  <div class="holder">
    <p class="holder-name">Rowan Jeffs</p>
    <p class="holder-title">Managing Director</p>
  </div>

  <p class="address">27 Vineyard Lane, Pokolbin<br>NSW Australia, 2320.</p>

  <ul class="contacts">
    <li><svg viewBox="0 0 12 12"><path d="M2.4 0.6l2 2-1 1.4c.6 1.5 1.9 2.8 3.4 3.4l1.4-1 2 2-1.3 1.8C5 10.4 1.6 7 .6 1.9z"/></svg>0412 987 654</li>
    <li><svg viewBox="0 0 12 12"><path d="M1 2.5h10v7H1z"/><path d="M1.6 3.2L6 6.6l4.4-3.4" fill="none" stroke="var(--orange)" stroke-width="1"/></svg>hello@ritajameson.art</li>
    <li><svg viewBox="0 0 12 12"><circle cx="6" cy="6" r="5.5"/><path d="M3 4.5c1 .3 1.5 1.3 1 2.2M7 2.5c.5 1 1.8 1.2 2.3 2.3M6 8.5c.8-.5 1.8-.2 2.5.8" fill="none" stroke="var(--orange)" stroke-width="1"/></svg>www.ritajameson.art</li>
  </ul>
</section>

<section class="card card-back">
  <div class="back-circle"></div>
  <h1 class="brand-name">Rita Jameson</h1>
  <p class="brand-tagline">ORIGINAL FINE ARTWORKS</p>
</section>

</body>
</html>
```